Maple Grove Schools | brand new stationery!

We need stationery design with our new logo! Our company updated it's name and image and we like to incorporate the new one on our stationery, business cards and email signature. We are looking for fresh, new ideas!
Industry: Childcare, Elementary and Middle School
Company Name: Maple Grove Schools
Tagline: Bright Futures Start Here
Main colors: Blue, white and a little yellow
Star shape is something new for us! Do you see a way to incorporate it as a design element?

```html
<!DOCTYPE html>
<html lang="en">
<head>
<meta charset="utf-8">
<title>Maple Grove Schools — Business Cards</title>
<link href="https://fonts.googleapis.com/css2?family=Montserrat:wght@400;500;600&display=swap" rel="stylesheet">
<style>
  :root {
    --navy: #0b1f78;
    --yellow: #fcc214;
    --white: #ffffff;
    --charcoal: #231f20;
    --silver: #c9c9cc;
    --ink: #4a4a4f;
    --backdrop: #d6d6d8;
  }
  * { box-sizing: border-box; margin: 0; padding: 0; }
  html, body { width: 1200px; height: 800px; overflow: hidden; }
  body {
    background: var(--backdrop);
    font-family: "Montserrat", Arial, sans-serif;
    position: relative;
  }
  .card {
    position: absolute;
    top: 245px;
    width: 540px;
    height: 310px;
    border-radius: 22px;
    border-bottom: 4px solid var(--yellow);
    border-right: 2px solid var(--yellow);
    overflow: hidden;
  }
  .card--front { left: 40px; background: var(--white); }
  .card--back { left: 620px; background: var(--charcoal); }

  .brand {
    position: absolute;
    display: flex;
    align-items: center;
    gap: 12px;
  }
  .brand__dot {
    width: 26px; height: 26px;
    border-radius: 50%;
    background: var(--yellow);
    flex: none;
  }
  .brand__name {
    font-weight: 600;
    line-height: 1.05;
  }
  .card--front .brand { top: 52px; right: 40px; }
  .card--front .brand__name { color: var(--navy); font-size: 34px; width: 230px; }

  .card--back .brand {
    top: 50%; left: 50%;
    transform: translate(-50%, -50%);
    flex-direction: column;
    gap: 18px;
    text-align: center;
  }
  .card--back .brand__name { color: var(--silver); font-size: 44px; }

  .person {
    position: absolute;
    left: 40px;
    top: 120px;
  }
  .person__name {
    color: var(--navy);
    font-weight: 600;
    font-size: 20px;
    letter-spacing: 0.5px;
    text-transform: uppercase;
  }
  .person__role {
    color: var(--yellow);
    font-size: 13px;
    font-weight: 500;
    margin-bottom: 10px;
  }
  .contacts { list-style: none; }
  .contacts li {
    display: flex;
    align-items: flex-start;
    gap: 9px;
    color: var(--ink);
    font-size: 11.5px;
    line-height: 1.45;
  }
  .contacts svg {
    width: 12px; height: 12px;
    margin-top: 2px;
    fill: var(--navy);
    flex: none;
  }
  .contacts .address { margin-bottom: 4px; }
</style>
</head>
<body>

<section class="card card--front">
  <div class="brand">
    <span class="brand__dot"></span>
    <span class="brand__name">Maple Grove Schools</span>
  </div>

  <div class="person">
    <p class="person__name">Daniel Harper</p>
    <p class="person__role">President</p>
    <ul class="contacts">
      <li class="address">
        <svg viewBox="0 0 12 12"><path d="M6 0a4 4 0 0 0-4 4c0 3 4 8 4 8s4-5 4-8a4 4 0 0 0-4-4zm0 5.5A1.5 1.5 0 1 1 6 2.5a1.5 1.5 0 0 1 0 3z"/></svg>
        <span>4120 Willow Bend Road<br>Fairbanks, Alaska 99701</span>
      </li>
      <li>
        <svg viewBox="0 0 12 12"><path d="M2.5 0.5l2 2.5-1 1.3c.7 1.6 1.9 2.8 3.5 3.5l1.3-1 2.5 2-1.2 2.2C5.2 10.7 1.3 6.8.3 1.7z"/></svg>
        <span>555-201-4830</span>
      </li>
      <li>
        <svg viewBox="0 0 12 12"><path d="M3 0h6v12H3zm1 1v8h4V1zm1.5 9h1v1h-1z" fill-rule="evenodd"/></svg>
        <span>555-318-2764</span>
      </li>
      <li>
        <svg viewBox="0 0 12 12"><path d="M3 0h6v3H3zM1 4h10v6H9v2H3v-2H1zm3 5v2h4V9z" fill-rule="evenodd"/></svg>
        <span>555-462-1095</span>
      </li>
      <li>
        <svg viewBox="0 0 12 12"><path d="M0 2h12v8H0zm1 1v.4l5 3.2 5-3.2V3z" fill-rule="evenodd"/></svg>
        <span>info@maplegrovekids.org</span>
      </li>
      <li>
        <svg viewBox="0 0 12 12"><path d="M6 0a6 6 0 1 0 0 12A6 6 0 0 0 6 0zm0 1.2c.8.9 1.3 2.3 1.4 4.2H4.6C4.7 3.5 5.2 2.1 6 1.2zM1.2 6.6h2.4c.1 1.6.5 3 1.1 4A4.8 4.8 0 0 1 1.2 6.6zm0-1.2A4.8 4.8 0 0 1 4.7 1.4c-.6 1-1 2.4-1.1 4zm4.8 5.4c-.8-.9-1.3-2.3-1.4-4.2h2.8c-.1 1.9-.6 3.3-1.4 4.2zm1.3-.2c.6-1 1-2.4 1.1-4h2.4a4.8 4.8 0 0 1-3.5 4zm1.1-5.2c-.1-1.6-.5-3-1.1-4a4.8 4.8 0 0 1 3.5 4z"/></svg>
        <span>maplegrovekids.org</span>
      </li>
    </ul>
  </div>
</section>

<section class="card card--back">
  <div class="brand">
    <span class="brand__dot"></span>
    <span class="brand__name">Maple Grove<br>Schools</span>
  </div>
</section>

</body>
</html>
```